WordPress Website Design for Multi-Brand Aviation Group (Unified Branding System)

Project Overview:
We are seeking a professional, modern WordPress website design for an aviation-focused umbrella company that owns and operates multiple subsidiary businesses. The goal is to create a cohesive visual system that clearly communicates that each company operates under the same parent organization, while still allowing each brand to maintain a slightly distinct identity.
This is not just a single website design—we are looking for a scalable design framework that can be applied across multiple aviation-related businesses.
Objectives:
- Establish a consistent, recognizable brand identity across all company websites
Clearly communicate the relationship between the parent company and its subsidiaries
-bCreate a clean, high-end corporate aviation aesthetic
- Ensure all designs are SEO-friendly and optimized for performance
- Allow flexibility for future expansion (additional subsidiaries)
- Target Audience:
- Corporate aviation clients
- Charter customers
- Students wishing to receive flight training
- Aircraft owners and operators
- Turbine aircraft training to meet insurance requirements
- Business professionals and high-net-worth individuals
- Aviation industry partners
Design Direction & Style:
We are looking for a premium, professional aviation feel—think clean, modern, and high-trust. The design should reflect the standards of corporate aviation: precision, safety, and sophistication.
Key style notes:
Minimalist but impactful layout
High-quality aviation photography (jets, interiors, operations, global travel)
Subtle motion/interaction (hover effects, transitions)
Clear typography hierarchy for readability and professionalism
Branding Requirements:
Incorporate the primary colors of the parent company logo across all designs
Website Structure (Core Pages):
Design a system that includes:
Home Page with the following links:
- About / Company Overview
- Aircraft Management
- Aircraft Acquisition
- Charter
- Pilot Services
- Trip Support
- Contact Page
Site should further include:
- Mobile-first responsive design
- Fast-loading, performance-optimized layouts
SEO & Technical Considerations:
- Design should support high-level SEO implementation:
- Clean layout structure that translates well to semantic HTML
- Proper heading hierarchy (H1, H2, H3)
- Space for keyword-rich content without clutter
- Optimized image placement (with alt text capability)
- Fast load times (lightweight design approach)
- Compatibility with WordPress SEO plugins (e.g., Yoast or Rank Math)
WordPress Requirements:
- Design should be easily built using WordPress (preferred builders: Elementor, Gutenberg, or similar)
- Reusable templates for scalability across multiple sites
- Easy for non-developers to update text and images
- Modular components (blocks/sections that can be reused across pages and sites)
- Navigation & UX:
- Simple, intuitive navigation
- Sticky header preferred
Style guide including:
- Colors
- Fonts
- Button styles
- Layout system
- Designs similar to high-end corporate aviation, private jet charter, or luxury service brands are preferred—clean, sharp, and premium without being overly flashy.
What We Want to Avoid:
- Overly busy layouts
- Generic templates with no brand identity
- Outdated or “stock” looking aviation designs
- Poor mobile responsiveness
Additional Notes:
We are building a long-term brand system, not just a one-off website. There is potential for ongoing work as we expand additional subsidiary sites.
We value designers who understand branding consistency across multiple business units and can create a scalable, professional system.
Include the attached main company logo "Vireton Aviation Group" and the "Member PJFO" logo on the main page.

```html
<!DOCTYPE html>
<html lang="en">
<head>
<meta charset="utf-8">
<title>Vireton Aviation Group</title>
<link rel="stylesheet" href="https://fonts.googleapis.com/css2?family=Michroma&family=Inter:wght@400;500;600;700&display=swap">
<style>
:root{
  --blue:#0a6fd8;
  --blue-deep:#0553b0;
  --navy:#061a2c;
  --ink:#0e2033;
  --body:#1f3f66;
  --pale:#eef5fc;
  --line:#c9d3de;
  --white:#ffffff;
}
*{box-sizing:border-box;margin:0;padding:0}
html,body{width:1200px;height:4622px;overflow:hidden}
body{position:relative;font-family:"Inter",sans-serif;color:var(--ink);background:var(--white)}
.abs{position:absolute}
.display{font-family:"Michroma",sans-serif;font-weight:400;letter-spacing:1.5px;text-transform:uppercase;white-space:nowrap}
.btn{position:absolute;display:flex;align-items:center;justify-content:center;background:var(--blue);color:var(--white);font-size:12px;font-weight:700;letter-spacing:2.5px;text-transform:uppercase}
.link-more{font-size:12px;font-weight:700;letter-spacing:2.5px;text-transform:uppercase;border-bottom:1.5px solid currentColor;padding-bottom:3px}
.brand-name{font-family:"Inter",sans-serif;font-weight:700;color:var(--blue);text-transform:uppercase;line-height:1.05}

/* hero */
.hero{position:absolute;left:0;top:0;width:1200px;height:870px;overflow:hidden;background:linear-gradient(180deg,#7e8c97 0%,#a9b3ba 35%,#6f7c86 60%,#3a444c 85%)}
.hero-photo{position:absolute;inset:0;background:radial-gradient(ellipse at 55% 55%,rgba(140,150,160,.6),transparent 60%)}
.hero-ghost{position:absolute;left:92px;top:530px;font-family:"Inter",sans-serif;font-weight:700;font-size:140px;letter-spacing:14px;color:rgba(255,255,255,.14)}
.topnav{position:absolute;top:12px;right:86px;display:flex;gap:40px;font-size:12px;letter-spacing:1px;color:#e8eef4}
.topnav .on{font-weight:700;color:var(--white)}
.mainnav{position:absolute;top:57px;left:301px;display:flex;gap:44px;font-size:12px;letter-spacing:1.2px;color:#eef2f6}
.header-rule{position:absolute;left:85px;top:95px;width:1029px;height:1px;background:rgba(255,255,255,.5)}
.hero h1{position:absolute;left:0;top:144px;width:1200px;text-align:center;color:var(--white);font-size:44px;line-height:62px;letter-spacing:3px}
.hero-text{position:absolute;left:190px;top:272px;width:820px;text-align:center;color:var(--white);font-size:16px;line-height:27px}
.hero-btn{position:absolute;left:504px;top:350px;width:192px;height:45px;border:1px solid rgba(255,255,255,.8);color:var(--white);font-size:12px;font-weight:700;letter-spacing:2.5px;display:flex;align-items:center;justify-content:center}
.slide-count{position:absolute;left:1097px;top:332px;color:var(--white);font-size:12px;text-align:center;width:18px}
.slide-count span{display:block}
.slide-count i{display:block;width:16px;height:1px;background:#fff;margin:8px auto 10px}

/* about */
.eyebrow{font-family:"Michroma",sans-serif;color:var(--blue);font-size:11px;letter-spacing:2px;text-transform:uppercase}
.sec-title{font-size:31px;line-height:42px;color:var(--ink)}
.copy{font-size:14px;line-height:25px;color:var(--body)}
.ph{position:absolute}

/* management */
.mgmt{position:absolute;left:0;top:1467px;width:1200px;height:788px;background:var(--pale)}
.card-cap{position:absolute;font-size:15px;letter-spacing:1px;color:var(--ink)}

/* pilot */
.pilot{position:absolute;left:0;top:2255px;width:1200px;height:657px;background:var(--navy);color:var(--white)}
.svc{position:absolute;top:273px;width:330px;height:300px;border:1px solid rgba(120,160,210,.55);border-bottom:3px solid var(--blue);padding:36px 30px 0}
.svc.is-active{background:var(--blue);border-color:var(--blue)}
.svc h3{font-size:18px;font-weight:500;margin:20px 0 14px;letter-spacing:.5px}
.svc p{font-size:14px;line-height:25px;color:#dfe8f3}
.svc .link-more{display:inline-block;margin-top:14px;color:var(--white)}

/* contact */
.contact{position:absolute;left:0;top:3543px;width:1200px;height:615px;background:var(--pale)}
.c-item{position:absolute;left:85px;display:flex;align-items:center;gap:14px;font-size:14px;line-height:21px;color:var(--body)}
.c-ico{width:36px;height:36px;border-radius:50%;background:#dde8f5;display:flex;align-items:center;justify-content:center;flex:none}
.form{position:absolute;left:477px;top:67px;width:637px;height:498px;background:var(--navy);border-radius:36px}
.field{position:absolute;border-bottom:1px solid #5d6e80;color:#dbe4ee;font-size:14px}

/* footer */
.footer{position:absolute;left:0;top:4158px;width:1200px;height:464px;background:var(--navy);color:var(--white)}
.f-head{position:absolute;font-family:"Michroma",sans-serif;font-size:13px;letter-spacing:1px}
.f-dash{position:absolute;width:26px;height:1px;background:#7a8a9c}
.f-links{position:absolute;font-size:14px;color:#dbe3ec;line-height:38px}
.social{position:absolute;top:4372px;width:46px;height:46px;border:1px solid rgba(255,255,255,.7);border-radius:50%}
</style>
</head>
<body>

<section class="hero" aria-label="Hero">
  <div class="hero-photo" role="img" aria-label="Fighter jet flying above grey clouds and mountains"></div>
  <div class="hero-ghost" aria-hidden="true">VIRETON</div>

  <div class="abs" style="left:85px;top:42px;display:flex;align-items:center;gap:10px">
    <span style="width:14px;height:14px;border-radius:50%;background:var(--blue)"></span>
    <span class="brand-name" style="font-size:17px;color:#fff">Vireton<br>Aviation Group</span>
  </div>
  <nav class="topnav"><span class="on">HOME</span><span>ABOUT</span><span>PILOT SERVICES</span></nav>
  <nav class="mainnav"><span>AIRCRAFT MANAGEMENT</span><span>AIRCRAFT ACQUISITION</span><span>CHARTER</span><span>TRIP SUPPORT</span></nav>
  <div class="btn" style="left:956px;top:43px;width:158px;height:43px;font-size:12px;letter-spacing:1.5px">CONTACT US</div>
  <div class="header-rule"></div>

  <h1 class="display">Discover the<br>Vireton Aviation Group</h1>
  <p class="hero-text">Lorem ipsum dolor sit amet, consectetur adipiscing elit. Vestibulum ornare quam ut massa laoreet dapibus. Morbi nec consequat dolor.</p>
  <div class="hero-btn">EXPLORE MORE ↗</div>
  <div class="slide-count"><span style="font-weight:700">01</span><i></i><span>03</span></div>

  <svg class="abs" style="left:0;top:690px" width="1200" height="180" viewBox="0 0 1200 180">
    <path d="M0 180 L0 158 C300 70 700 20 1200 20 L1200 180 Z" fill="var(--blue-deep)"/>
    <path d="M0 180 C300 95 700 42 1200 34 L1200 180 Z" fill="#ffffff"/>
  </svg>
</section>

<section aria-label="About">
  <div class="abs eyebrow" style="left:85px;top:978px">About</div>
  <h2 class="abs display sec-title" style="left:85px;top:1003px;width:470px;white-space:normal">Vireton Aviation Group</h2>
  <p class="abs copy" style="left:85px;top:1107px;width:470px">Lorem ipsum dolor sit amet, consectetur ading elit, sed do eiusmod tempor incididunt ut labore et dolore magna aliqua. Quis ipsum suspendisse ultricavida. Risus commodo vira maecenas accumsan lacus vel facilisis. Mauris pulvinar commodo elit ut malesuada. Duis maximus semper posuere. Nulla varius arcu vel posuere tincidunt. Morbi volutpat imperdiet nulla.</p>
  <div class="btn" style="left:85px;top:1288px;width:159px;height:49px">READ MORE ↗</div>
  <div class="ph" role="img" aria-label="Aircraft wing against a purple and orange sunset" style="left:870px;top:888px;width:244px;height:478px;background:linear-gradient(180deg,#5b4fa8 0%,#c2507a 35%,#e8623a 60%,#8c1d10 100%)"></div>
  <div class="ph" role="img" aria-label="Fighter jet banking against a clear blue sky" style="left:626px;top:958px;width:424px;height:339px;background:linear-gradient(160deg,#3d8fe3,#1f6fd0)"></div>
</section>

<section class="mgmt" aria-label="Aircraft management">
  <h2 class="abs display" style="left:0;top:72px;width:1200px;text-align:center;font-size:31px">Aircraft Management</h2>
  <p class="abs copy" style="left:230px;top:116px;width:740px;text-align:center">Lorem ipsum dolor sit amet, consectetur ading elit, sed do eiusmod tempor incididunt ut labore et dolore magna aliqua. Quis ipsum suspendisse ultricavida.</p>
  <div class="ph" role="img" aria-label="Aircraft on tarmac" style="left:0;top:266px;width:36px;height:436px;background:linear-gradient(180deg,#7c8794,#4c545c)"></div>
  <div class="ph" role="img" aria-label="Vintage bomber parked on an airfield" style="left:54px;top:266px;width:351px;height:436px;background:linear-gradient(180deg,#3f7fd0 0%,#9fb9d6 50%,#5b5f66 100%)"></div>
  <div class="ph" role="img" aria-label="Traveller in red jacket on a mountain ridge at sunset" style="left:423px;top:209px;width:350px;height:436px;background:linear-gradient(180deg,#2c5c9c 0%,#c89a6f 40%,#4f6b3a 75%,#2f3c26 100%)"></div>
  <div class="card-cap" style="left:423px;top:667px">INNOVATION</div>
  <div class="abs link-more" style="left:660px;top:664px;color:var(--blue)">READ MORE ↗</div>
  <div class="ph" role="img" aria-label="Airliner flying over a coastal old town" style="left:789px;top:266px;width:352px;height:436px;background:linear-gradient(180deg,#a9c6e6 0%,#cfdbe6 40%,#5fa8a0 70%,#b8643e 100%)"></div>
  <div class="ph" role="img" aria-label="Aircraft on tarmac" style="left:1159px;top:266px;width:41px;height:436px;background:linear-gradient(180deg,#8b949c,#565d63)"></div>
</section>

<section class="pilot" aria-label="Pilot services">
  <h2 class="abs display" style="left:85px;top:144px;font-size:31px;color:#fff">Pilot Services</h2>
  <p class="abs" style="left:613px;top:120px;width:505px;font-size:14px;line-height:25px;color:#fff">Lorem ipsum dolor sit amet, consectetur ading elit, sed do eiusmod tempor incididunt ut lab et dolore magna aliqua. Quis ipsum suspendisse ultricavida.</p>

  <article class="svc" style="left:85px">
    <svg width="36" height="36" viewBox="0 0 36 36"><circle cx="14" cy="10" r="6" fill="#fff"/><rect x="6" y="18" width="16" height="16" rx="3" fill="var(--blue)"/><path d="M24 14 L34 10" stroke="#fff" stroke-width="2"/></svg>
    <h3>PILOT SERVICE 01</h3>
    <p>Lorem ipsum dolor sitet, consectetur adip elit. Aenean viverra interdum arcu sed pretium. Pelleue elementum felis turpis.</p>
    <span class="link-more">READ MORE ↗</span>
  </article>
  <article class="svc is-active" style="left:434px">
    <svg width="50" height="36" viewBox="0 0 50 36"><path d="M8 6l2 4 4 .5-3 3 .8 4-3.8-2-3.8 2 .8-4-3-3 4-.5z M25 2l2 4 4 .5-3 3 .8 4-3.8-2-3.8 2 .8-4-3-3 4-.5z M42 6l2 4 4 .5-3 3 .8 4-3.8-2-3.8 2 .8-4-3-3 4-.5z" fill="#fff"/><path d="M4 24h42M10 30h30" stroke="#fff" stroke-width="3"/></svg>
    <h3>PILOT SERVICE 02</h3>
    <p>Lorem ipsum dolor sitet, consectetur adip elit. Aenean viverra interdum arcu sed pretium. Pelleue elementum felis turpis.</p>
    <span class="link-more">READ MORE ↗</span>
  </article>
  <article class="svc" style="left:784px">
    <svg width="60" height="36" viewBox="0 0 60 36"><circle cx="9" cy="12" r="5" fill="#fff"/><rect x="4" y="19" width="10" height="15" rx="2" fill="#fff"/><path d="M22 18 L58 8 M24 24 L56 18" stroke="var(--blue)" stroke-width="3"/></svg>
    <h3>PILOT SERVICE 03</h3>
    <p>Lorem ipsum dolor sitet, consectetur adip elit. Aenean viverra interdum arcu sed pretium. Pelleue elementum felis turpis.</p>
    <span class="link-more">READ MORE ↗</span>
  </article>
</section>

<section aria-label="Trip support">
  <div class="ph" role="img" aria-label="Jet trainer aircraft in flight" style="left:147px;top:3016px;width:386px;height:425px;background:linear-gradient(180deg,#e3eefa,#d6e6f7)"></div>
  <div class="abs eyebrow" style="left:613px;top:3058px">Trip Support</div>
  <h2 class="abs display sec-title" style="left:613px;top:3076px">Our Trip Support</h2>
  <p class="abs" style="left:613px;top:3130px;width:510px;font-size:14px;line-height:24px;font-weight:600;color:var(--ink)">Lorem ipsum dolor sit amet, consectetur ading elit, sed do eiusmod tempor incididunt ut labet dolore magna aliqua. Quis ipsse ultricavida.</p>
  <p class="abs copy" style="left:613px;top:3196px;width:500px;border-left:2px solid #8db6e6;padding-left:20px">Nullam vehicula, lectus id consequat ultricies, lacus ligula tincidunt sem, in volutpat quam nisi ut nisi. Nulla facilisi. Maecenas feugiat congue suscipit. Duis volutpat posuere posuere. Praesent id tellus massa. Etiam auctor elit in placerat accumsan. Integer vulputate posuere commodo.</p>
  <div class="btn" style="left:613px;top:3344px;width:158px;height:47px">READ MORE ↗</div>
</section>

<section class="contact" aria-label="Contact">
  <h2 class="abs display" style="left:85px;top:220px;font-size:31px">Contact Us</h2>
  <div class="c-item" style="top:285px">
    <span class="c-ico"><svg width="14" height="16" viewBox="0 0 14 16"><path d="M7 0a6 6 0 0 0-6 6c0 4.5 6 10 6 10s6-5.5 6-10a6 6 0 0 0-6-6z" fill="var(--blue)"/><circle cx="7" cy="6" r="2.2" fill="#fff"/></svg></span>
    <span>27 Airfield Way, Suite 4<br>Brisbane, Australia</span>
  </div>
  <div class="c-item" style="top:342px">
    <span class="c-ico"><svg width="14" height="11" viewBox="0 0 14 11"><rect width="14" height="11" rx="1.5" fill="var(--blue)"/><path d="M1 1.5l6 4.5 6-4.5" stroke="#fff" stroke-width="1.3" fill="none"/></svg></span>
    <span>info@viretonaviationgroup.com</span>
  </div>
  <div class="c-item" style="top:385px">
    <span class="c-ico"><svg width="14" height="14" viewBox="0 0 14 14"><path d="M3 0l3 3-1.6 2.2a9 9 0 0 0 4.4 4.4L11 8l3 3-2 3C6 14 0 8 0 2z" fill="var(--blue)"/></svg></span>
    <span>1800-555-017</span>
  </div>

  <form class="form" aria-label="Get in touch">
    <h2 class="abs display" style="left:40px;top:34px;font-size:31px;color:#fff">Get in Touch</h2>
    <div class="field" style="left:40px;top:102px;width:269px;height:43px">First Name</div>
    <div class="field" style="left:332px;top:102px;width:269px;height:43px">Last Name</div>
    <div class="field" style="left:40px;top:172px;width:561px;height:41px">Email</div>
    <div class="field" style="left:40px;top:242px;width:561px;height:41px">Phone</div>
    <div class="field" style="left:40px;top:313px;width:561px;height:79px">How can we help you</div>
    <div class="btn" style="left:443px;top:412px;width:158px;height:47px">SUBMIT ↗</div>
  </form>
</section>

<footer class="footer">
  <div class="abs" style="left:85px;top:84px;display:flex;align-items:center;gap:12px">
    <span style="width:18px;height:18px;border-radius:50%;background:var(--blue)"></span>
    <span class="brand-name" style="font-size:24px">Vireton<br>Aviation Group</span>
  </div>
  <div class="f-head" style="left:466px;top:98px">QUICK LINKS</div>
  <div class="f-dash" style="left:466px;top:135px"></div>
  <div class="f-links" style="left:466px;top:154px">Home<br>About<br>Aircraft Management<br>Aircraft Acquisition</div>
  <div class="f-links" style="left:660px;top:154px">Charter<br>Pilot Services<br>Trip Support<br>Contact</div>
  <div class="f-head" style="left:849px;top:98px">SUPPORT US</div>
  <div class="f-dash" style="left:849px;top:135px"></div>
  <div class="abs" style="left:849px;top:167px;display:flex;align-items:center;gap:16px" role="img" aria-label="Member PJFO">
    <span style="width:62px;height:62px;border-radius:50%;background:var(--blue-deep)"></span>
    <span style="font-size:14px;line-height:1.2">member of<br><span style="font-size:30px;font-weight:600;letter-spacing:3px">PJFO</span></span>
  </div>
  <div class="abs" style="left:85px;top:390px;width:1029px;height:1px;background:#2a3d52"></div>
  <div class="abs" style="left:85px;top:420px;font-size:14px;color:#dbe3ec">© 2026 <span style="color:var(--blue)">Vireton-Aviation-Group.</span> All right reserved.</div>
  <div class="abs" style="right:86px;top:420px;font-size:14px;color:#dbe3ec">April 28, 2026. Layout_4</div>
</footer>
<span class="social" style="left:83px" aria-label="Social profile 1"></span>
<span class="social" style="left:138px" aria-label="Social profile 2"></span>
<span class="social" style="left:192px" aria-label="Social profile 3"></span>
<span class="social" style="left:248px" aria-label="Social profile 4"></span>

</body>
</html>
```